History of Bramwell Fixture Services Inc

This is to be a large poster (48" x 16' Landscape Orientation) printed by a large format printer. The poster through text and photos will represent the history of our company. The file called "Timeline List 20150318" has the events by date order. Maybe this shouldn't be under poster but we didn't see another category that applied.
Reason: We needed to better organize the pictures and content. We cut down the number of pictures and "event" to 105 instead of the 300 some it was before.
Reason: Upon request i have extended the deadline. I apologize for any inconvenience. I'm new to pixel forum. Let me know if you have anymore feed back from me.
Target Market(s)
This will be the center piece of our office for both customers and clients to view.
Industry/Entity Type
Landscape
Look and feel
Each slider illustrates characteristics of the customer's brand and the style your logo design should communicate.

```html
<!DOCTYPE html>
<html lang="en">
<head>
<meta charset="utf-8">
<title>History of Bramwell Fixture Services Inc</title>
<link rel="stylesheet" href="https://fonts.googleapis.com/css2?family=Open+Sans:wght@300;400;600;700&display=swap">
<style>
  :root {
    --bg-top: #8d9c99;
    --bg-mid: #e4e6e5;
    --orange: #f2603f;
    --ink: #2b2b2b;
    --muted: #8a8a8a;
    --white: #ffffff;
    --brand-red: #d8262e;
  }
  * { box-sizing: border-box; margin: 0; padding: 0; }
  html, body { width: 1200px; height: 1200px; overflow: hidden; }
  body {
    font-family: "Open Sans", sans-serif;
    background: linear-gradient(180deg, var(--bg-top) 0%, var(--bg-mid) 32%, var(--bg-mid) 68%, var(--bg-top) 100%);
    position: relative;
  }
  .timeline {
    position: absolute; left: 0; top: 400px; width: 1200px; height: 400px;
    background: linear-gradient(180deg, #f4f4f4 0%, #f0f0f0 40%, #e2e2e2 62%, #f4f4f4 100%);
    overflow: hidden;
  }
  .timeline-band {
    position: absolute; left: 0; top: 58px; width: 1200px; height: 137px;
    background: linear-gradient(90deg, #f06a4b 0%, var(--orange) 50%, #f06a4b 100%);
    opacity: .92;
  }
  .timeline-frames { position: absolute; left: 0; top: 0; }
  .photo {
    position: absolute; border: 2px solid var(--white); border-radius: 6px;
    box-shadow: 0 1px 3px rgba(0,0,0,.35);
  }
  .abs { position: absolute; }
  .body-text { font-size: 8.4px; line-height: 12.4px; color: var(--ink); }
  .heading-white { color: var(--white); font-weight: 600; font-size: 15px; }
  .heading-dark { color: var(--ink); font-weight: 600; font-size: 18px; line-height: 25px; }
  .vertical { transform-origin: left top; transform: rotate(-90deg); white-space: nowrap; color: var(--ink); font-weight: 600; }
  .lead-text { font-size: 11px; line-height: 16.8px; color: var(--ink); }
  .year { font-weight: 300; font-size: 44px; color: #9a9a9a; letter-spacing: 1px; }
  .brand-name { color: var(--brand-red); font-weight: 700; font-size: 19px; line-height: 22px; text-align: center; }
</style>
</head>
<body>
<section class="timeline">
  <div class="timeline-band"></div>
  <svg class="timeline-frames" width="1200" height="400" viewBox="0 0 1200 400">
    <g fill="none" stroke="#ffffff" stroke-width="2" opacity=".9">
      <rect x="10" y="35" width="30" height="30"/>
      <rect x="45" y="12" width="32" height="32"/>
      <rect x="35" y="60" width="25" height="25"/>
      <rect x="626" y="38" width="46" height="46"/>
      <rect x="962" y="18" width="92" height="92"/>
      <rect x="1000" y="40" width="34" height="34"/>
      <rect x="477" y="260" width="92" height="110"/>
      <rect x="557" y="270" width="30" height="70"/>
      <rect x="595" y="255" width="40" height="40"/>
    </g>
  </svg>
</section>

<div class="photo" role="img" aria-label="Portrait photo of the two company founders" style="left:54px;top:496px;width:101px;height:140px;background:linear-gradient(160deg,#8f8a82,#d9d4cc);"></div>
<p class="abs" style="left:72px;top:639px;font-size:9px;line-height:12.5px;color:var(--muted);">Founded by Daniel<br>and Carla Whitford</p>
<div class="abs vertical year" style="left:24px;top:744px;">1991</div>
<div class="abs brand-name" style="left:78px;top:718px;width:164px;">Bramwell Fixture<br>Services Inc</div>

<div class="photo" role="img" aria-label="Commercial lighting crew standing in front of company trucks" style="left:183px;top:436px;width:110px;height:74px;background:linear-gradient(180deg,#d8dde3,#6b8f5a);"></div>
<div class="abs vertical" style="left:181px;top:690px;font-size:17px;">Commercial Lighting</div>
<p class="abs body-text" style="left:204px;top:513px;width:100px;">With 24/7 Emergency Service and Day and Night Crews, our Team is ready to service Maryland, Virginia and Washington DC.</p>

<div class="abs heading-white" style="left:322px;top:471px;">Sports Lighting</div>
<div class="photo" role="img" aria-label="Stadium light pole installation on a sports field" style="left:321px;top:495px;width:104px;height:76px;background:linear-gradient(180deg,#5b8bd1,#a9c4e8 60%,#8a7a55);"></div>
<p class="abs body-text" style="left:322px;top:577px;width:106px;">Bramwell Fixture Services Inc (BFS) has about 15 years experience in the sportslighting business, during this time we have constructed fields. These fields include Baseball, Softball, Lacrosse, Soccer, Football, Basketball, Multi-use, and Field Hockey</p>

<div class="photo" role="img" aria-label="Bucket truck installing street lights along a highway" style="left:473px;top:415px;width:144px;height:108px;background:linear-gradient(180deg,#7aa3d9,#c9d6e3 45%,#7f8284);"></div>
<div class="abs vertical" style="left:474px;top:580px;font-size:17px;line-height:21px;">Street<br>Lights</div>
<p class="abs body-text" style="left:521px;top:527px;width:116px;">Our crews are installing a new energy efficient street light system in Arlington Virginia.We installed new conduits using the latest Directional Drilling methods and technology.</p>

<div class="photo" role="img" aria-label="White company service van" style="left:660px;top:475px;width:123px;height:72px;background:linear-gradient(180deg,#9a9a9a,#e8e8e8 55%,#7d7d7d);"></div>
<div class="abs heading-white" style="left:663px;top:546px;font-size:14.5px;">Electrical Services</div>
<p class="abs body-text" style="left:663px;top:571px;width:136px;font-size:8px;">Here at Bramwell Fixture Services Inc. (BFS) we employ many licensed Journeyman and Master Electricians in Maryland, Virginia, and Washington DC. All of which are capable of repairing, maintaining, or installing all types of electoral equipment including but not limited to panel boards, breakers, disconnect switches, fuses, contactors, exit lights, emergency light packs, receptacles, air compressors, lights, fans, motors, smoke detectors, signs, and heater.</p>

<div class="abs heading-dark" style="left:814px;top:437px;">Northen Virginia<br>Operations</div>
<div class="photo" role="img" aria-label="Fleet of company bucket trucks parked at the office" style="left:813px;top:490px;width:142px;height:79px;background:linear-gradient(180deg,#6f8fae,#ececec 55%,#6a6a6a);"></div>
<p class="abs lead-text" style="left:817px;top:574px;width:145px;">We have a fully staffed and equipped office in Springfield Virginia. This office handles commercial service, State DOT, local governments and special projects</p>

<div class="photo" role="img" aria-label="Work zone with cones and trucks on a neighborhood street" style="left:993px;top:547px;width:130px;height:72px;background:linear-gradient(180deg,#6e9c4e,#c8cfc8 55%,#7a7a7a);"></div>
<div class="abs heading-dark" style="left:997px;top:620px;">Maintenance of<br>Traffic (MOT)</div>
<p class="abs lead-text" style="left:998px;top:673px;width:150px;">Bramwell Fixture Services Inc. provides MOT whether on a neighborhood street or a super highway.</p>
</body>
</html>
```